Design material for Lumora Event

We need a design of POSM for Lumora Event
1. Content:
- The Lumora Event 3rd
- Singapore 28.10.2018
- A placeholder for insert logo of sponsors (limit 10 logo)
2. POSM:
- Backdrop: 5,5m and 2,6m
- Banner: 4m and 0,5m
- Standee: 0,8m and 2m
- Cover: A4 size
3. Style:
We need style simply because we are a hospital.
Main color: light blue and a little of green (if can)

Hope to see your design soon!

Font styles to use
Sans Serif

Colors
0792cd
85cae6
86cfc6
33b8a4
33a6d7

```html
<!DOCTYPE html>
<html lang="en">
<head>
<meta charset="utf-8">
<title>Lumora Event — 3rd Edition Cover</title>
<link rel="stylesheet" href="https://fonts.googleapis.com/css2?family=Montserrat:wght@200;300;500;700;800&family=Quicksand:wght@400;500&display=swap">
<style>
  :root {
    --blue-deep: #0a5e8a;
    --blue: #0792cd;
    --blue-soft: #33a6d7;
    --sky: #85cae6;
    --mint: #86cfc6;
    --teal: #33b8a4;
    --green-num: #8cc9a6;
    --grey-text: #8a8a8a;
    --grey-mail: #9a9a9a;
    --rule: #cfe6e1;
    --paper: #ffffff;
  }
  * { margin: 0; padding: 0; box-sizing: border-box; }
  html, body { width: 848px; height: 1200px; overflow: hidden; }
  body { background: var(--paper); font-family: "Montserrat", sans-serif; }
  .cover {
    position: relative; width: 848px; height: 1200px; overflow: hidden;
    background: linear-gradient(180deg, #ececec 0%, #f6f6f6 35%, #ffffff 60%, #ffffff 100%);
  }
  .edition {
    position: absolute; left: 0; width: 100%; top: 196px;
    text-align: center; color: var(--green-num);
    font-weight: 800; font-size: 124px; line-height: 1;
    padding-left: 30px;
  }
  .edition sup { font-size: 28px; font-weight: 500; vertical-align: top; position: relative; top: 20px; margin-left: 2px; }
  .title-light, .title-bold {
    position: absolute; left: 0; width: 100%; text-align: center;
    color: var(--blue-deep); line-height: 1; padding-left: 30px;
  }
  .title-light { top: 308px; font-weight: 200; font-size: 70px; letter-spacing: 1px; }
  .title-bold { top: 368px; font-weight: 700; font-size: 92px; letter-spacing: 2px; }
  .city {
    position: absolute; top: 474px; left: 0; width: 100%; text-align: center; padding-left: 30px;
    color: var(--teal); font-weight: 700; font-size: 15px; letter-spacing: 10px;
  }
  .date { position: absolute; top: 494px; left: 316px; display: flex; align-items: center; }
  .date-words { display: flex; flex-direction: column; align-items: flex-end; line-height: 1; }
  .date-day { color: var(--teal); font-weight: 300; font-size: 30px; }
  .date-month { color: var(--teal); font-weight: 700; font-size: 21px; letter-spacing: 1px; margin-top: 2px; }
  .date-num { color: var(--blue); font-weight: 300; font-size: 68px; line-height: 1; margin-left: 2px; letter-spacing: -2px; }
  .year {
    position: absolute; top: 560px; left: 0; width: 100%; text-align: center; padding-left: 30px;
    color: var(--blue-deep); font-weight: 300; font-size: 19px; letter-spacing: 26px;
  }
  .rule { position: absolute; top: 602px; left: 207px; width: 424px; height: 1px; background: var(--rule); }
  .intro {
    position: absolute; top: 622px; left: 209px; width: 400px;
    font-family: "Quicksand", sans-serif; font-size: 13.3px; line-height: 16.8px; color: var(--grey-text);
  }
  .sponsors {
    position: absolute; top: 768px; left: 61px; width: 716px; height: 69px; background: var(--paper);
    display: flex; align-items: center; justify-content: space-between; padding: 0 12px;
  }
  .sponsor {
    display: flex; align-items: center; gap: 4px;
    font-family: "Montserrat", sans-serif; font-weight: 700; font-size: 8.5px;
    color: var(--blue-deep); text-transform: uppercase; line-height: 1.15; text-align: center;
  }
  .sponsor .mark { width: 7px; height: 7px; background: var(--sky); border-radius: 50%; flex: none; }
  .contact {
    position: absolute; top: 864px; left: 0; width: 100%; text-align: center; padding-left: 30px;
    font-weight: 500; font-size: 14px; color: var(--grey-mail);
  }
  .skyline {
    position: absolute; left: 0; bottom: 0; width: 848px; height: 282px;
    background: linear-gradient(180deg, rgba(255,255,255,0) 0%, #d9d9d9 30%, #9e9e9e 62%, #6d6d6d 78%, #c9c9c9 88%, #e2e2e2 100%);
  }
</style>
</head>
<body>
  <main class="cover">
    <div class="edition">3<sup>rd</sup></div>
    <h1>
      <span class="title-light">LUMORA</span>
      <span class="title-bold">EVENT</span>
    </h1>
    <div class="city">SINGAPORE</div>
    <div class="date">
      <div class="date-words">
        <span class="date-day">SUNDAY</span>
        <span class="date-month">OCTOBER</span>
      </div>
      <span class="date-num">28</span>
    </div>
    <div class="year">2018</div>
    <div class="rule"></div>
    <p class="intro">At vero eos et accusamus et iusto odio dignissimos ducimus qui blanditiis praesentium voluptatum deleniti atque corrupti quos dolores et quas molestias excepturi sint occaecati cupiditate non provident, similique sunt in culpa qui officia deserunt mollitia animi, id est laborum et dolorum fuga.</p>
    <section class="sponsors" aria-label="Sponsors">
      <div class="sponsor"><span class="mark"></span>Bluewave<br>Rafting</div>
      <div class="sponsor">Pinecrest</div>
      <div class="sponsor">Fernhill<br>Farm</div>
      <div class="sponsor">Kestra<br>Boats</div>
      <div class="sponsor">Oakmill<br>Bakery</div>
      <div class="sponsor">Northbay<br>Paddle Club</div>
      <div class="sponsor">trailnova</div>
      <div class="sponsor">Halvern<br>Spirits</div>
      <div class="sponsor">Riverline<br>Kayak</div>
      <div class="sponsor"><span class="mark"></span>Sixpoint<br>Gear</div>
    </section>
    <div class="contact">LumoraEvent@lumoramail.org</div>
    <div class="skyline" role="img" aria-label="Black and white photograph of the Singapore waterfront skyline with towers and glass domes over the bay"></div>
  </main>
</body>
</html>
```